CopperWanderer Stretching and Strength

We need a application design for a our first IOS application. the goal of the application is to categorize stretching and strength routines for triathlon.

We would like to see designs that use the color orange.

The design of the application should be compliant with the last version of the IOS Mobile.

For this first design we need the folowing pages:

1- Sign up
2- Log in
3- Home
4- View Exercises
5- Do it
6- Profile

The description of each page is in the attached document.

We need a logo design for the application. The logo should express that mission of the application that is for stretch and strength training for Triathlon.

We will use https://pellavokit.example to develop the application, if you have any experience of the limitation that this technology have it will be a plus.

If you have any question please feel free to contact us.

Reason: We will extend the deadline to be sure that we select the best design from all of you. we will take the final decision next Tuesday.

Target Market(s)

The market for my aplicación is the Running a Triathlon world.

Logo Text

CopperWanderer

Font styles to use
Serif

Colors
f37122
ffffff
dcdcdc

Requirements
Must have
• In some future we will add more features in the menu. We should considere it for the design.
• The designs should include all the screens in the power point.

```html
<!DOCTYPE html>
<html lang="en">
<head>
<meta charset="utf-8">
<title>CopperWanderer – App Screens</title>
<link rel="stylesheet" href="https://fonts.googleapis.com/css2?family=Roboto:wght@400;500;700&display=swap">
<style>
:root{
  --orange:#f37122;
  --white:#ffffff;
  --grey:#dcdcdc;
  --canvas:#ebecef;
  --backdrop:#d3e2f1;
  --ink:#333840;
  --muted:#7a7f87;
  --label:#5a5e63;
  --social:#2c5bb4;
  --tag-flex:#2bb3e6;
  --tag-leg:#b566e0;
  --tag-pain:#5b5de0;
  --tag-shoulder:#f2c230;
}
*{box-sizing:border-box;margin:0;padding:0}
html,body{width:1200px;height:1200px;overflow:hidden}
body{background:var(--backdrop);font-family:'Roboto',sans-serif;color:var(--ink);position:relative}

.screen{position:absolute;width:206px;height:365px;background:var(--canvas);overflow:hidden;border-radius:3px;box-shadow:0 6px 18px rgba(40,60,90,.18)}
.screen-title{position:absolute;width:284px;text-align:center;font-size:34px;font-weight:500;color:#55595e}
.abs{position:absolute}

.status{position:absolute;top:0;left:0;right:0;height:14px;background:var(--orange);color:var(--white);font-size:5px;display:flex;align-items:center;justify-content:space-between;padding:0 4px}
.appbar{position:absolute;top:14px;left:0;right:0;height:22px;background:var(--orange);color:var(--white);font-size:8px;font-weight:500;display:flex;align-items:center;justify-content:center}
.appbar .menu{position:absolute;left:8px;top:8px;width:8px;height:6px;border-top:1px solid #fff;border-bottom:1px solid #fff}
.appbar .menu::after{content:"";position:absolute;left:0;right:0;top:2px;border-top:1px solid #fff}
.appbar .back{position:absolute;left:6px;top:5px}
.appbar .filter{position:absolute;right:6px;top:6px}

.field{position:absolute;left:14px;width:178px;height:19px;background:var(--white);border:1px solid #e2e3e6;font-size:6.5px;color:var(--muted);display:flex;align-items:center;justify-content:space-between;padding:0 7px}
.field svg{width:7px;height:7px;fill:#8a8e94}
.btn{position:absolute;left:14px;width:178px;height:21px;border-radius:11px;background:var(--orange);color:var(--white);font-size:7px;font-weight:500;display:flex;align-items:center;justify-content:center}
.note{position:absolute;left:0;right:0;text-align:center;font-size:5.5px;color:var(--label)}
.note b{color:var(--orange);font-weight:500;text-decoration:underline}
.or{position:absolute;left:99px;width:8px;height:8px;border-radius:50%;background:var(--white);font-size:3.5px;display:flex;align-items:center;justify-content:center;color:var(--label)}
.social{position:absolute;left:0;right:0;bottom:0;height:26px;display:flex;font-size:6.5px}
.social div{flex:1;display:flex;align-items:center;gap:5px;padding-left:8px}
.social .link{background:var(--social);color:var(--white)}
.social .mail{background:var(--white);color:var(--ink)}
.social i{width:11px;height:11px;border-radius:50%;display:block}
.social .link i{background:var(--white)}
.social .mail i{background:var(--orange)}
.social em{font-size:5px}
.check{display:inline-block;width:6px;height:6px;border:1px solid #a0a4aa;background:#fff;vertical-align:middle;position:relative}
.check.on{border-color:var(--orange)}
.check.on::after{content:"";position:absolute;left:1.3px;top:0;width:2px;height:3.5px;border:solid var(--orange);border-width:0 1px 1px 0;transform:rotate(45deg)}

.card{position:absolute;left:6px;right:6px;background:var(--white);box-shadow:0 1px 2px rgba(0,0,0,.08)}
.routine{display:flex;gap:6px;padding:5px 5px 4px;background:var(--white)}
.thumb{flex:none;width:30px;height:28px;background:linear-gradient(135deg,#6f8db3,#c9b79a 60%,#8a6f5c)}
.routine-body{flex:1;min-width:0}
.routine-title{font-size:6.5px;color:var(--ink);line-height:1.2}
.tags{display:flex;gap:2px;margin:2px 0}
.tag{font-size:3px;color:#fff;border-radius:3px;padding:1px 4px;line-height:1}
.tag-flex{background:var(--tag-flex)}.tag-leg{background:var(--tag-leg)}.tag-pain{background:var(--tag-pain)}.tag-shoulder{background:var(--tag-shoulder)}
.routine-desc{font-size:4.5px;color:var(--muted);line-height:1.35}
.routine-meta{font-size:4.2px;color:var(--muted);margin-top:2px}
.routine-meta b{color:var(--orange);font-weight:400}
.routine-meta span{margin-left:7px}

/* loading */
.splash{background:var(--orange);color:var(--white);text-align:center}
.splash .mark{position:absolute;left:85px;top:100px;width:36px;height:36px;border-radius:50%;background:var(--white)}
.splash .name{position:absolute;top:162px;left:0;right:0;font-size:12px;font-weight:500;letter-spacing:.3px}
.splash .tagline{position:absolute;top:180px;left:0;right:0;font-size:5.5px}
.splash .foot{position:absolute;top:323px;left:0;right:0;font-size:7.5px}
.splash .ver{position:absolute;top:347px;left:0;right:0;font-size:5.5px}

/* home chart */
.tabs{display:flex;justify-content:space-around;font-size:5px;color:var(--muted);padding:6px 10px 0}
.tabs .on{color:var(--orange)}
.section-head{display:flex;justify-content:space-between;font-size:6px;color:var(--ink);padding:6px 8px 4px}
.section-head span{color:var(--orange);font-size:4.5px}
.sponsors{position:absolute;left:6px;top:322px;display:flex;gap:3px}
.sponsor{width:56px;height:32px;background:var(--white);display:flex;align-items:center;justify-content:center;gap:3px;font-size:6px;font-weight:700;color:var(--ink)}
.sponsor i{width:6px;height:6px;background:var(--orange);display:block}

/* filter */
.dim{position:absolute;inset:0;background:rgba(0,0,0,.62)}
.filter-panel{position:absolute;left:0;right:0;top:188px;bottom:0;background:var(--canvas);font-size:6px;color:var(--label)}
.filter-row{position:absolute;left:10px;display:flex;align-items:center}
.filter-row .k{width:29px;color:var(--ink);font-size:6.5px}
.opt{display:inline-flex;align-items:center;gap:4px;margin-right:10px}

/* do it */
.toggle{position:absolute;left:41px;top:42px;width:124px;height:16px;border-radius:8px;background:var(--white);display:flex;overflow:hidden;font-size:6px}
.toggle div{flex:1;display:flex;align-items:center;justify-content:center;gap:3px;color:var(--orange)}
.toggle .on{background:var(--orange);color:var(--white)}
.toggle i{width:6px;height:5px;display:block;border:1px solid currentColor;border-radius:1px}
.video{position:absolute;left:2px;right:2px;top:4px;height:102px;background:linear-gradient(180deg,#a9c3dc 0%,#d5dde2 45%,#8bb36a 70%,#6f9a4d 100%)}
.play{position:absolute;left:80px;top:42px;width:18px;height:14px;border-radius:3px;background:var(--orange)}
.play::after{content:"";position:absolute;left:7px;top:4px;border-left:5px solid #fff;border-top:3px solid transparent;border-bottom:3px solid transparent}
.progress{position:absolute;left:3px;right:3px;top:18px;height:15px;background:#eeeff1}
.progress div{width:31%;height:100%;background:var(--orange);font-size:4px;color:#fff;padding:5px 0 0 20px}

/* profile */
.avatar{position:absolute;left:22px;top:51px;width:48px;height:48px;border-radius:50%;background:radial-gradient(circle at 50% 40%,#c79a7c,#6b8e54)}
.info-row{position:absolute;left:6px;right:6px;display:flex;justify-content:space-between;font-size:6.8px;color:var(--ink)}
.info-row span:last-child{color:var(--label)}
</style>
</head>
<body>

<!-- Row 1 -->
<section class="screen splash" style="left:70px;top:88px">
  <div class="status"><span>●●●○○ NOVA</span><span>4:21 PM</span><span>100%</span></div>
  <div class="mark"></div>
  <div class="name">COPPERWANDERER</div>
  <div class="tagline">Stretch and strength training for Triathlon</div>
  <div class="foot">Lorem ipsum dolor sit amet</div>
  <div class="ver">v 0.0.2</div>
</section>
<div class="screen-title" style="left:31px;top:520px">Loading</div>

<section class="screen login" style="left:354px;top:88px">
  <div class="status"><span>●●●○○ NOVA</span><span>4:21 PM</span><span>100%</span></div>
  <div class="note" style="top:72px;font-size:12px;color:var(--orange)">Welcome to <b style="text-decoration:none;font-weight:500">CopperWanderer</b></div>
  <div class="note" style="top:92px;font-size:7px">Stretch and Strength training for Triathlon</div>
  <div class="field" style="top:142px">User Name <svg viewBox="0 0 10 10"><circle cx="5" cy="3" r="2.3"/><path d="M1 10a4 4 0 0 1 8 0z"/></svg></div>
  <div class="field" style="top:167px">Password <svg viewBox="0 0 10 10"><rect x="1.5" y="4.5" width="7" height="5.5"/><path d="M3 4.5V3a2 2 0 0 1 4 0v1.5" fill="none" stroke="#8a8e94" stroke-width="1.2"/></svg></div>
  <div class="abs" style="top:196px;left:14px;right:14px;display:flex;justify-content:space-between;font-size:5.5px;color:var(--muted)"><span><i class="check"></i> Remamber Me</span><em>Forgot Password?</em></div>
  <div class="btn" style="top:224px">LOG IN</div>
  <div class="note" style="top:291px">You have not any account yet? <b>SIGN UP</b> now</div>
  <div class="or" style="top:315px">OR</div>
  <div class="social"><div class="link"><i></i>Log in <em>with</em> Linkbook</div><div class="mail"><i></i>Log in <em>with</em> Mailora</div></div>
</section>
<div class="screen-title" style="left:315px;top:520px">Log In</div>

<section class="screen signup" style="left:637px;top:88px">
  <div class="status"><span>●●●○○ NOVA</span><span>4:21 PM</span><span>100%</span></div>
  <svg class="abs" style="left:6px;top:22px" width="10" height="8" viewBox="0 0 10 8"><path d="M9 4H1M4 1L1 4l3 3" fill="none" stroke="#777" stroke-width="0.9"/></svg>
  <div class="abs" style="left:80px;top:29px;width:46px;height:46px;border-radius:50%;background:#d6d7da;border:2px solid #fff"></div>
  <div class="note" style="top:80px;font-size:4.5px">ADD YOUR PHOTO</div>
  <div class="field" style="top:102px">Full Name <svg viewBox="0 0 10 10"><circle cx="5" cy="3" r="2.3"/><path d="M1 10a4 4 0 0 1 8 0z"/></svg></div>
  <div class="field" style="top:126px">Email Id <svg viewBox="0 0 10 10"><rect x="0.5" y="2" width="9" height="6"/></svg></div>
  <div class="field" style="top:150px;width:86px">Age <svg viewBox="0 0 10 10"><rect x="1" y="2" width="8" height="7" fill="none" stroke="#8a8e94"/></svg></div>
  <div class="field" style="top:150px;left:104px;width:88px">Gender: <svg viewBox="0 0 10 10"><path d="M2 4h6L5 7z"/></svg></div>
  <div class="field" style="top:175px">Sport: <svg viewBox="0 0 10 10"><path d="M2 4h6L5 7z"/></svg></div>
  <div class="field" style="top:199px">User Name <svg viewBox="0 0 10 10"><circle cx="5" cy="3" r="2.3"/><path d="M1 10a4 4 0 0 1 8 0z"/></svg></div>
  <div class="field" style="top:223px">Password <svg viewBox="0 0 10 10"><rect x="1.5" y="4.5" width="7" height="5.5"/><path d="M3 4.5V3a2 2 0 0 1 4 0v1.5" fill="none" stroke="#8a8e94" stroke-width="1.2"/></svg></div>
  <div class="abs" style="top:251px;left:14px;font-size:5.5px;color:var(--muted)"><i class="check on"></i> Receive Email</div>
  <div class="btn" style="top:276px">CREATE ACCOUNT</div>
  <div class="note" style="top:303px">You already have an account? <b>LOG IN</b> now</div>
  <div class="or" style="top:322px">OR</div>
  <div class="social"><div class="link"><i></i>Sign up <em>with</em> Linkbook</div><div class="mail"><i></i>Sign up <em>with</em> Mailora</div></div>
</section>
<div class="screen-title" style="left:598px;top:520px">Sign Up</div>

<section class="screen home" style="left:921px;top:88px">
  <div class="status"><span>●●●○○ NOVA</span><span>4:21 PM</span><span>100%</span></div>
  <div class="appbar"><i class="menu"></i>HOME</div>
  <div class="card" style="top:42px;height:108px">
    <div class="tabs"><span class="on">Today</span><span>Yesterday</span><span>This Week</span><span>This Month</span></div>
    <svg width="194" height="94" viewBox="0 0 194 94" style="display:block">
      <text x="97" y="6" font-size="5.5" text-anchor="middle" fill="#333840" font-family="Roboto,sans-serif">Total Routines: (1/3)</text>
      <text x="17" y="44" font-size="3.5" fill="#7a7f87" transform="rotate(-90 17 44)" font-family="Roboto,sans-serif">Lorem ipsum</text>
      <line x1="22" y1="18" x2="22" y2="82" stroke="#e4e5e8" stroke-width="0.5"/>
      <line x1="22" y1="82" x2="180" y2="82" stroke="#e4e5e8" stroke-width="0.5"/>
      <g stroke="#eeeff1" stroke-width="0.4"><line x1="46" y1="18" x2="46" y2="82"/><line x1="70" y1="18" x2="70" y2="82"/><line x1="94" y1="18" x2="94" y2="82"/><line x1="118" y1="18" x2="118" y2="82"/><line x1="142" y1="18" x2="142" y2="82"/><line x1="166" y1="18" x2="166" y2="82"/></g>
      <rect x="37" y="53" width="16" height="29" fill="#f37122"/>
      <rect x="86" y="43" width="16" height="39" fill="#f37122"/>
      <rect x="134" y="68" width="16" height="14" fill="#f37122"/>
      <g font-size="4" fill="#7a7f87" text-anchor="middle" font-family="Roboto,sans-serif">
        <text x="45" y="50">Lorem ipsum</text><text x="94" y="40">Lorem ipsum</text><text x="142" y="65">Lorem ipsum</text>
        <text x="22" y="90">10am</text><text x="46" y="90">11am</text><text x="70" y="90">12pm</text><text x="94" y="90">1pm</text><text x="118" y="90">2pm</text><text x="142" y="90">3pm</text><text x="166" y="90">4pm</text>
      </g>
      <circle cx="5" cy="31" r="5" fill="#eeeff1"/><path d="M6 29l-2 2 2 2" fill="none" stroke="#999" stroke-width="0.6"/>
      <circle cx="189" cy="31" r="5" fill="#eeeff1"/><path d="M188 29l2 2-2 2" fill="none" stroke="#555" stroke-width="0.6"/>
    </svg>
  </div>
  <div class="card" style="top:156px;height:144px;overflow:hidden">
    <div class="section-head">History <span>See More</span></div>
    <div class="routine" style="border-bottom:1px solid #eee"><div class="thumb" role="img" aria-label="Group stretching outdoors photo"></div><div class="routine-body"><p class="routine-title">Lorem ipsum dolor sit amet</p><div class="tags"><span class="tag tag-flex">Flexibility</span><span class="tag tag-leg">Leg</span><span class="tag tag-pain">Pain Relief</span></div><p class="routine-desc">Lorem ipsum dolor sit amet, consectetur adipiscing elit. Etiam vitae eros efficitur...</p><p class="routine-meta"><b>Time:</b> 5:32 min<span><b>Level:</b> Moderate</span></p></div></div>
    <div class="routine" style="border-bottom:1px solid #eee"><div class="thumb" role="img" aria-label="Class stretching indoors photo" style="background:linear-gradient(135deg,#b86a55,#e0c3a8 55%,#5b6f9a)"></div><div class="routine-body"><p class="routine-title">Lorem ipsum dolor sit amet</p><div class="tags"><span class="tag tag-flex">Flexibility</span><span class="tag tag-pain">Pain Relief</span></div><p class="routine-desc">Lorem ipsum dolor sit amet, consectetur adipiscing elit. Etiam vitae eros efficitur...</p><p class="routine-meta"><b>Time:</b> 4:25 min<span><b>Level:</b> Easy</span></p></div></div>
    <div class="routine"><div class="thumb" style="height:6px" role="img" aria-label="Stretching photo"></div><div class="routine-body"><p class="routine-title" style="color:var(--muted)">Lorem ipsum dolor sit amet</p></div></div>
  </div>
  <div class="abs" style="left:14px;top:310px;font-size:6px">Sponsors</div>
  <div class="sponsors">
    <div class="sponsor"><i></i>Stridewell</div>
    <div class="sponsor"><i></i>ValueMart</div>
    <div class="sponsor"><i></i>Innhaven</div>
  </div>
</section>
<div class="screen-title" style="left:882px;top:520px">Home</div>

<!-- Row 2 -->
<section class="screen activity" style="left:70px;top:672px">
  <div class="status"><span>●●●○○ NOVA</span><span>4:21 PM</span><span>100%</span></div>
  <div class="appbar"><i class="menu"></i>STRENGTH EXERCISE<svg class="filter" width="8" height="8" viewBox="0 0 8 8"><path d="M0 0h8L5 4v4L3 7V4z" fill="#fff"/></svg></div>
  <div class="abs" style="left:0;right:0;top:37px;height:15px;background:#fff;font-size:6px;color:var(--muted);display:flex;align-items:center;gap:4px;padding-left:8px"><svg width="6" height="6" viewBox="0 0 6 6"><circle cx="2.5" cy="2.5" r="1.8" fill="none" stroke="#555" stroke-width="0.7"/><path d="M4 4l1.7 1.7" stroke="#555" stroke-width="0.7"/></svg>Search here...</div>
  <div class="abs" style="left:6px;right:6px;top:58px;display:flex;flex-direction:column;gap:4px">
    <div class="routine"><div class="thumb" role="img" aria-label="Group stretching outdoors photo"></div><div class="routine-body"><p class="routine-title">Lorem ipsum dolor sit amet</p><div class="tags"><span class="tag tag-flex">Flexibility</span><span class="tag tag-leg">Leg</span><span class="tag tag-pain">Pain Relief</span></div><p class="routine-desc">Lorem ipsum dolor sit amet, consectetur adipiscing elit. Etiam vitae eros efficitur...</p><p class="routine-meta"><b>Time:</b> 5:32 min<span><b>Level:</b> Moderate</span></p></div></div>
    <div class="routine"><div class="thumb" role="img" aria-label="Person stretching on mat photo" style="background:linear-gradient(135deg,#e9e4df,#c9a58f 60%,#7a8aa3)"></div><div class="routine-body"><p class="routine-title">Lorem ipsum dolor sit amet</p><div class="tags"><span class="tag tag-flex">Flexibility</span><span class="tag tag-leg">Leg</span><span class="tag tag-shoulder">Shoulder</span></div><p class="routine-desc">Lorem ipsum dolor sit amet, consectetur adipiscing elit. Etiam vitae eros efficitur...</p><p class="routine-meta"><b>Time:</b> 4:25 min<span><b>Level:</b> Easy</span></p></div></div>
    <div class="routine"><div class="thumb" role="img" aria-label="Floor stretch photo" style="background:linear-gradient(135deg,#f1ece6,#d8c2b0 55%,#9aa7b8)"></div><div class="routine-body"><p class="routine-title">Lorem ipsum dolor sit amet</p><div class="tags"><span class="tag tag-flex">Flexibility</span><span class="tag tag-pain">Pain Relief</span></div><p class="routine-desc">Lorem ipsum dolor sit amet, consectetur adipiscing elit. Etiam vitae eros efficitur...</p><p class="routine-meta"><b>Time:</b> 3:10 min<span><b>Level:</b> Moderate</span></p></div></div>
    <div class="routine"><div class="thumb" role="img" aria-label="Leg stretch photo" style="background:linear-gradient(135deg,#f4f1ee,#c8708a 55%,#5d7fb0)"></div><div class="routine-body"><p class="routine-title">Lorem ipsum dolor sit amet</p><div class="tags"><span class="tag tag-leg">Leg</span><span class="tag tag-pain">Pain Relief</span></div><p class="routine-desc">Lorem ipsum dolor sit amet, consectetur adipiscing elit. Etiam vitae eros efficitur...</p><p class="routine-meta"><b>Time:</b> 4:00 min<span><b>Level:</b> Moderate</span></p></div></div>
    <div class="routine"><div class="thumb" role="img" aria-label="Yoga class photo" style="background:linear-gradient(135deg,#c45a3f,#e8b48a 55%,#4a6fa8)"></div><div class="routine-body"><p class="routine-title">Lorem ipsum dolor sit amet</p><div class="tags"><span class="tag tag-pain">Pain Relief</span></div><p class="routine-desc">Lorem ipsum dolor sit amet, consectetur adipiscing elit. Etiam vitae eros efficitur...</p><p class="routine-meta"><b>Time:</b> 5:09 min<span><b>Level:</b> Easy</span></p></div></div>
    <div class="routine"><div class="thumb" role="img" aria-label="Standing stretch photo" style="background:linear-gradient(135deg,#eee,#a08a70 55%,#333)"></div><div class="routine-body"><p class="routine-title">Lorem ipsum dolor sit amet</p><div class="tags"><span class="tag tag-flex">Flexibility</span><span class="tag tag-leg">Leg</span></div><p class="routine-desc">Lorem ipsum dolor sit amet, consectetur adipiscing elit. Etiam</p></div></div>
  </div>
</section>
<div class="screen-title" style="left:31px;top:1104px">View Activity</div>

<section class="screen filter-screen" style="left:354px;top:672px">
  <div class="status"><span>●●●○○ NOVA</span><span>4:21 PM</span><span>100%</span></div>
  <div class="appbar"><i class="menu"></i>STRENGTH EXERCISE<svg class="filter" width="8" height="8" viewBox="0 0 8 8"><path d="M0 0h8L5 4v4L3 7V4z" fill="#fff"/></svg></div>
  <div class="abs" style="left:0;right:0;top:37px;height:15px;background:#fff;font-size:6px;color:var(--muted);display:flex;align-items:center;padding-left:18px">Search here...</div>
  <div class="abs" style="left:6px;right:6px;top:58px;display:flex;flex-direction:column;gap:4px">
    <div class="routine"><div class="thumb" role="img" aria-label="Group stretching outdoors photo"></div><div class="routine-body"><p class="routine-title">Lorem ipsum dolor sit amet</p><div class="tags"><span class="tag tag-flex">Flexibility</span><span class="tag tag-leg">Leg</span><span class="tag tag-pain">Pain Relief</span></div><p class="routine-desc">Lorem ipsum dolor sit amet, consectetur adipiscing elit. Etiam vitae eros efficitur...</p><p class="routine-meta"><b>Time:</b> 5:32 min<span><b>Level:</b> Moderate</span></p></div></div>
    <div class="routine"><div class="thumb" role="img" aria-label="Person stretching on mat photo" style="background:linear-gradient(135deg,#e9e4df,#c9a58f 60%,#7a8aa3)"></div><div class="routine-body"><p class="routine-title">Lorem ipsum dolor sit amet</p><div class="tags"><span class="tag tag-flex">Flexibility</span><span class="tag tag-leg">Leg</span><span class="tag tag-shoulder">Shoulder</span></div><p class="routine-desc">Lorem ipsum dolor sit amet, consectetur adipiscing elit. Etiam vitae eros efficitur...</p><p class="routine-meta"><b>Time:</b> 4:25 min<span><b>Level:</b> Easy</span></p></div></div>
    <div class="routine"><div class="thumb" role="img" aria-label="Floor stretch photo"></div><div class="routine-body"><p class="routine-title">Lorem ipsum dolor sit amet</p></div></div>
  </div>
  <div class="dim"></div>
  <div class="filter-panel">
    <div class="abs" style="top:10px;left:0;right:0;text-align:center;font-size:8.5px;color:var(--ink)">Filter</div>
    <div class="filter-row" style="top:35px"><span class="k">Tags:</span><span class="opt"><i class="check on"></i>Flexibility</span><span class="opt"><i class="check"></i>Pain Relief</span><span class="opt"><i class="check on"></i>Shoulder</span></div>
    <div class="filter-row" style="top:50px"><span class="k"></span><span class="opt"><i class="check"></i>Leg</span></div>
    <div class="filter-row" style="top:71px"><span class="k">Sport:</span><span class="opt"><i class="check on"></i>Running</span><span class="opt"><i class="check"></i>Bike</span><span class="opt"><i class="check on"></i>Swimming</span></div>
    <div class="filter-row" style="top:92px"><span class="k">Time:</span><span class="opt"><i class="check on"></i>Approximate time of exercise or routine.</span></div>
    <div class="filter-row" style="top:114px"><span class="k">Level:</span><span class="opt"><i class="check on"></i>Easy</span><span class="opt"><i class="check on"></i>Moderate</span><span class="opt"><i class="check"></i>Advanced</span></div>
    <div class="btn" style="top:145px">APPLY FILTER</div>
  </div>
</section>
<div class="screen-title" style="left:315px;top:1104px">Filter_Popup</div>

<section class="screen doit" style="left:637px;top:672px">
  <div class="status"><span>●●●○○ NOVA</span><span>4:21 PM</span><span>100%</span></div>
  <div class="appbar"><svg class="back" width="10" height="10" viewBox="0 0 10 10"><path d="M9 5H1M4 2L1 5l3 3" fill="none" stroke="#fff" stroke-width="0.9"/></svg>DO IT</div>
  <div class="toggle"><div><i></i>Image</div><div class="on"><i></i>Video</div></div>
  <div class="card" style="top:66px;height:218px">
    <div class="video" role="img" aria-label="Video still of a group doing tai chi stretches on a lawn"><div class="play"></div></div>
    <div class="abs" style="left:3px;right:3px;top:114px">
      <p class="routine-title" style="font-size:7.5px">Lorem ipsum dolor sit amet</p>
      <div class="tags"><span class="tag tag-flex">Flexibility</span><span class="tag tag-leg">Leg</span><span class="tag tag-pain">Pain Relief</span></div>
      <p class="routine-desc" style="font-size:5.3px;line-height:1.4">Lorem ipsum dolor sit amet, consectetur adipiscing elit. Etiam vitae eros efficitur, finibus sapien et, porta libero. Integer facilisis massa dolor. Vivamus tempor enim sit amet lectus vehicula, eget luctus quam dignissim. Sed eu accumsan lacus. Nam et ullamcorper magna. Integer id diam varius arcu vestibulum porttitor.</p>
      <p class="routine-meta" style="font-size:5.5px;margin-top:6px"><b>Time:</b> 5:32 min</p>
      <p class="routine-meta" style="font-size:5.5px;margin-top:4px"><b>Level:</b> Moderate</p>
    </div>
  </div>
  <div class="card" style="top:288px;height:36px">
    <div class="abs" style="left:3px;top:5px;font-size:6px">Timer</div>
    <div class="abs" style="right:3px;top:7px;font-size:4px;color:var(--muted)">Lorem ipsum</div>
    <div class="progress"><div>18%</div></div>
  </div>
  <div class="btn" style="top:336px">START</div>
</section>
<div class="screen-title" style="left:598px;top:1104px">Do It</div>

<section class="screen profile" style="left:921px;top:672px">
  <div class="status"><span>●●●○○ NOVA</span><span>4:21 PM</span><span>100%</span></div>
  <div class="appbar"><i class="menu"></i>PROFILE</div>
  <div class="avatar" role="img" aria-label="Profile photo of the user"></div>
  <div class="abs" style="left:84px;top:62px;font-size:9px;font-weight:500">Dario Mendes</div>
  <div class="abs" style="left:84px;top:78px;font-size:7px;color:var(--orange)">dario.mendes98@mailora.example</div>
  <div class="info-row" style="top:124px"><span>Full Name</span><span style="color:var(--orange)">Dario</span></div>
  <div class="abs" style="left:90px;right:6px;top:134px;border-top:1px solid #c9cbd0"></div>
  <div class="info-row" style="top:145px"><span>Username</span><span>dariomendes98</span></div>
  <div class="info-row" style="top:167px"><span>Age</span><span>25</span></div>
  <div class="info-row" style="top:188px"><span>Gender</span><span>Male</span></div>
  <div class="info-row" style="top:210px"><span>Email Id</span><span>dario.mendes98@mailora.example</span></div>
  <div class="info-row" style="top:231px"><span>City</span><span>Berkeley, US</span></div>
  <div class="info-row" style="top:252px"><span>Sports</span><span>Bike and Running</span></div>
  <div class="btn" style="top:331px">SAVE</div>
</section>
<div class="screen-title" style="left:882px;top:1104px">Profile</div>

</body>
</html>
```